Create a memorable Web Design for real estate branding

we are a Minnepolis brokerage and boutique housing specialist with over 27 years of experience in the Global furnished housing industry, servicing the Greater Los Angeles area. Specializing in “warm environments” we offer a customized approach to satisfying our guests and client’s needs by offering a wide array of options in highly desirable areas. Additionally, Lantern Dwelling Partners offers assistance and expertise to home buyers, sellers and investors.

Industry/Entity Type

Real Estate

Number of Pages Required

1 page

Font styles to use
Serif
Sans Serif
Decorative

```html
<!DOCTYPE html>
<html lang="en">
<head>
<meta charset="utf-8">
<title>Corvin Lake Real Estate</title>
<link rel="stylesheet" href="https://fonts.googleapis.com/css2?family=Roboto+Condensed:wght@400;700&family=Open+Sans:wght@400;600&display=swap">
<style>
:root{
  --teal:#17a88b;
  --teal-dark:#0f9a7e;
  --lime:#9dc73b;
  --ink:#333;
  --muted:#555;
  --navy:#1d2f6e;
  --cream:#fcfbf4;
  --mist:#f3f4f7;
  --footer-dark:#262626;
  --line:#e3e3e3;
}
*{box-sizing:border-box;margin:0;padding:0}
html,body{width:1200px;height:2647px;overflow:hidden}
body{font-family:"Open Sans",sans-serif;color:var(--ink);background:#fff;position:relative}
.heading{font-family:"Roboto Condensed",sans-serif}
.topline{height:4px;background:#3a3a3a;position:relative}
.topline::after{content:"";position:absolute;left:400px;width:300px;top:0;height:4px;background:var(--teal)}
.header{position:relative;height:137px}
.brand{position:absolute;left:99px;top:36px;font-family:"Roboto Condensed",sans-serif;font-weight:700;color:var(--teal);line-height:1}
.brand .name{font-size:44px;display:block}
.brand .sub{font-size:22px;letter-spacing:1px;display:block;margin-left:96px;margin-top:2px}
.contact-mini{position:absolute;left:658px;top:50px;display:flex;gap:10px;align-items:center;font-size:14px;color:var(--teal);line-height:1.3}
.contact-mini .mail{color:var(--muted)}
.search{position:absolute;left:868px;top:54px;width:234px;height:38px;border:1px solid var(--line);font-size:12px;color:#777;padding:10px 14px;display:flex;justify-content:space-between;align-items:center}
.nav{position:absolute;left:99px;top:141px;width:1002px;height:53px;background:var(--teal);display:flex;align-items:center;z-index:2}
.nav .home{width:92px;height:53px;background:#4a4a4a;display:flex;align-items:center;justify-content:center}
.nav a{color:#fff;text-decoration:none;font-size:14px;padding:0 32px;font-family:"Open Sans",sans-serif;font-weight:600;letter-spacing:.2px}
.hero{position:absolute;top:194px;left:0;width:1200px;height:524px;background:linear-gradient(180deg,#9aa9b6 0%,#c9b79a 38%,#6b7a62 62%,#2f7fa4 82%,#3c8fbf 100%)}
.hero .arrow{position:absolute;top:248px;width:36px;height:36px;border-radius:50%;background:rgba(30,30,30,.7);display:flex;align-items:center;justify-content:center}
.hero-title{position:absolute;left:369px;top:268px;width:462px;height:117px;background:rgba(40,40,40,.55);color:#fff;font-family:"Roboto Condensed",sans-serif;font-weight:700;font-size:40px;line-height:42px;text-align:center;padding-top:16px}
.about-band{position:absolute;top:718px;left:0;width:1200px;height:521px;background:var(--cream)}
.feature-panel{position:absolute;left:86px;top:648px;width:1026px;height:310px;background:#f4f4ef;z-index:1}
.features{position:absolute;left:99px;top:660px;display:flex;gap:11px;z-index:2}
.feature{width:326px;height:298px;background:var(--teal);color:#fff;text-align:center;padding-top:26px;box-shadow:0 8px 10px rgba(0,0,0,.18)}
.feature.alt{background:var(--lime)}
.feature .ring{width:88px;height:88px;border:2px solid #fff;border-radius:50%;margin:0 auto;display:flex;align-items:center;justify-content:center}
.feature h3{font-family:"Roboto Condensed",sans-serif;font-weight:400;font-size:19px;margin:22px 0 10px}
.feature p{font-size:11.5px;line-height:19px;padding:0 28px}
.feature .go{width:30px;height:30px;border:1px solid rgba(255,255,255,.7);border-radius:50%;margin:24px auto 0;display:flex;align-items:center;justify-content:center}
.about{position:absolute;top:1006px;left:150px;width:900px;text-align:center}
.about h2{font-family:"Roboto Condensed",sans-serif;font-weight:400;font-size:30px;color:var(--ink)}
.about p{font-size:12px;line-height:21px;color:var(--muted);margin-top:12px}
.btn{display:inline-block;margin-top:22px;background:var(--teal);color:#fff;font-family:"Roboto Condensed",sans-serif;font-size:16px;padding:12px 32px;border:2px solid #fff;box-shadow:0 0 0 1px var(--teal)}
.listings{position:absolute;top:1239px;left:0;width:1200px;height:778px;background:var(--mist)}
.listings h2{position:absolute;top:57px;width:100%;text-align:center;font-family:"Roboto Condensed",sans-serif;font-weight:400;font-size:30px}
.listings h2 span{color:var(--navy)}
.grid{position:absolute;left:102px;top:125px;display:grid;grid-template-columns:repeat(4,231px);column-gap:25px;row-gap:25px}
.card{height:280px;background:#fffdf5;border:1px solid #e6e6e0;padding:5px}
.card .photo{height:171px}
.card p{font-size:11px;line-height:19px;color:var(--muted);padding:12px 8px 8px}
.card .meta{display:flex;justify-content:space-between;border-top:1px solid #ece9dc;font-size:11.5px;color:var(--muted);height:38px;align-items:center;padding-left:8px}
.card .meta .price{border-left:1px solid #ece9dc;padding:0 8px;height:100%;display:flex;align-items:center}
.news{position:absolute;top:2017px;left:0;width:1200px;height:334px;border-top:1px solid var(--line)}
.news h2{position:absolute;left:97px;top:92px;transform:translateY(-50%);font-family:"Roboto Condensed",sans-serif;font-weight:400;font-size:21px}
.news .item{position:absolute;top:108px;display:flex;gap:28px;width:480px}
.news .photo{width:185px;height:164px;flex:none}
.news h4{font-family:"Roboto Condensed",sans-serif;font-weight:400;font-size:17px;color:var(--muted)}
.news .date{font-size:12px;color:#7aa52a;font-weight:600;margin:14px 0 10px}
.news p{font-size:11.5px;line-height:21px;color:var(--muted)}
.news .more{font-size:12px;margin-top:6px;color:var(--ink)}
.footer{position:absolute;top:2351px;left:0;width:1200px;height:236px;background:var(--teal);color:#fff}
.footer .brand{color:#fff;top:36px}
.footer .brand .name{font-size:36px}
.footer .brand .sub{font-size:18px;margin-left:90px}
.footer .blurb{position:absolute;left:99px;top:100px;width:250px;font-size:11.5px;line-height:20px}
.footer h5{font-family:"Roboto Condensed",sans-serif;font-weight:400;font-size:18px;margin-bottom:18px}
.fcol{position:absolute;top:38px;font-size:12px;line-height:24px}
.fcol .row{display:flex;gap:14px;align-items:center}
.newsletter{display:flex;margin-top:18px}
.newsletter .field{width:152px;height:40px;background:#fff;color:#555;font-size:11px;padding:12px}
.newsletter .sub{width:98px;height:40px;background:#2c2c2c;font-size:12px;display:flex;align-items:center;justify-content:center}
.bottom{position:absolute;top:2587px;left:0;width:1200px;height:60px;background:var(--footer-dark);color:#999;font-size:11px}
.bottom .copy{position:absolute;left:97px;top:22px}
.socials{position:absolute;left:975px;top:16px;display:flex;gap:6px}
.socials span{width:22px;height:22px;border:1px solid #aaa;border-radius:50%}
</style>
</head>
<body>
<div class="topline"></div>
<header class="header">
  <div class="brand"><span class="name">Corvin Lake</span><span class="sub">Real Estate</span></div>
  <div class="contact-mini">
    <svg width="34" height="34" viewBox="0 0 34 34"><circle cx="17" cy="17" r="15.5" fill="none" stroke="#17a88b" stroke-width="1.5"/><path d="M12 10c1-1 2 0 3 2s0 2-1 3c1 2 3 4 5 5 1-1 1-2 3-1s3 2 2 3c-2 3-5 2-8-1s-6-7-4-11z" fill="#17a88b"/></svg>
    <div><div>+1 555 010 2040</div><div class="mail">info@corvinlake.com</div></div>
  </div>
  <div class="search">search
    <svg width="12" height="12" viewBox="0 0 12 12"><circle cx="5" cy="5" r="3.8" fill="none" stroke="#555" stroke-width="1.5"/><path d="M8 8l3 3" stroke="#555" stroke-width="1.5"/></svg>
  </div>
</header>
<nav class="nav">
  <div class="home"><svg width="22" height="20" viewBox="0 0 22 20"><path d="M11 1L1 10h3v9h5v-6h4v6h5v-9h3z" fill="#fff"/></svg></div>
  <a>ABOUT US</a><a>OUR SERVICES</a><a>PROPERTIES</a><a>REAL ESTATE &amp; BROKERAGE</a><a>CONTACT US</a>
</nav>
<section class="hero" role="img" aria-label="Photo of a two-storey white villa with lit windows and a pool at dusk">
  <div class="arrow" style="left:46px"><svg width="10" height="14" viewBox="0 0 10 14"><path d="M8 1L2 7l6 6" fill="none" stroke="#fff" stroke-width="2.5"/></svg></div>
  <div class="arrow" style="right:46px"><svg width="10" height="14" viewBox="0 0 10 14"><path d="M2 1l6 6-6 6" fill="none" stroke="#fff" stroke-width="2.5"/></svg></div>
  <h1 class="hero-title">SPECIALIZING IN<br>“WARM ENVIRONMENTS”</h1>
</section>
<div class="about-band"></div>
<div class="feature-panel"></div>
<div class="features">
  <div class="feature">
    <div class="ring"><svg width="32" height="28" viewBox="0 0 22 20"><path d="M11 1L1 10h3v9h5v-6h4v6h5v-9h3z" fill="#fff"/></svg></div>
    <h3>BUYING A HOME</h3>
    <p>Lorem ipsum dolor sit amet, consectetur adipiscing elit, sed do eiusmod tempor incididunt ut labore et dolore magna aliqua.</p>
    <div class="go"><svg width="10" height="10" viewBox="0 0 10 10"><path d="M1 1l8 8M9 3v6H3" fill="none" stroke="#fff" stroke-width="1.2"/></svg></div>
  </div>
  <div class="feature alt">
    <div class="ring"><span class="heading" style="font-size:40px;font-weight:700">$</span></div>
    <h3>BOUTIQUE HOUSING</h3>
    <p>Lorem ipsum dolor sit amet, consectetur adipiscing elit, sed do eiusmod tempor incididunt ut labore et dolore magna aliqua.</p>
    <div class="go"><svg width="10" height="10" viewBox="0 0 10 10"><path d="M1 1l8 8M9 3v6H3" fill="none" stroke="#fff" stroke-width="1.2"/></svg></div>
  </div>
  <div class="feature">
    <div class="ring"><svg width="34" height="34" viewBox="0 0 24 24"><path d="M2 10h4v11H2zM8 10l4-8c2 0 3 1 2.5 3L14 9h6c1.5 0 2.3 1.3 2 2.5l-2 8c-.3 1-1 1.5-2 1.5H8z" fill="none" stroke="#fff" stroke-width="1.6" stroke-linejoin="round"/></svg></div>
    <h3>BEST PRICE GUARANTEE!</h3>
    <p>Lorem ipsum dolor sit amet, consectetur adipiscing elit, sed do eiusmod tempor incididunt ut labore et dolore magna aliqua.</p>
    <div class="go"><svg width="10" height="10" viewBox="0 0 10 10"><path d="M1 1l8 8M9 3v6H3" fill="none" stroke="#fff" stroke-width="1.2"/></svg></div>
  </div>
</div>
<section class="about">
  <h2>ABOUT OUR COMPANY</h2>
  <p>Lorem ipsum dolor sit amet, consectetur adipiscing elit, sed do eiusmod tempor incididunt ut labore et dolore magna aliqua. Ut enim ad minim veniam, quis nostrud exercitation ullamco laboris nisi ut aliquip ex ea commodo consequat. Duis aute irure dolor in reprehenderit in voluptate velit esse cillum dolore eu fugiat nulla pariatur. Excepteur sint occaecat cupidatat non proident, sunt in culpa qui officia deserunt mollit anim</p>
  <span class="btn">VIEW MORE INFO</span>
</section>
<section class="listings">
  <h2>PROPERTIES <span>LISTINGS</span></h2>
  <div class="grid">
    <div class="card"><div class="photo" role="img" aria-label="Photo of a suburban house with porch and lawn" style="background:linear-gradient(180deg,#8fb8e0,#b9a68a 55%,#5f9a3c)"></div><p>Lorem ipsum dolor sit amet, consetur adipiscing elit, sed do eiusmod</p><div class="meta"><span>📍&#xFE0E; Los Angeles, Califonia</span><span class="price">$370,000</span></div></div>
    <div class="card"><div class="photo" role="img" aria-label="Photo of waterfront apartment towers at dusk" style="background:linear-gradient(180deg,#3e4f88,#b97f5e 55%,#3b3f6a)"></div><p>Lorem ipsum dolor sit amet, consetur adipiscing elit, sed do eiusmod</p><div class="meta"><span>📍&#xFE0E; Los Angeles, Califonia</span><span class="price">$370,000</span></div></div>
    <div class="card"><div class="photo" role="img" aria-label="Photo of a villa with pool at night" style="background:linear-gradient(180deg,#29496e,#c28a52 55%,#2b86a8)"></div><p>Lorem ipsum dolor sit amet, consetur adipiscing elit, sed do eiusmod</p><div class="meta"><span>📍&#xFE0E; Los Angeles, Califonia</span><span class="price">$370,000</span></div></div>
    <div class="card"><div class="photo" role="img" aria-label="Photo of a lit patio with dining table and pool" style="background:linear-gradient(180deg,#2c2c30,#b38a52 55%,#4a4a46)"></div><p>Lorem ipsum dolor sit amet, consetur adipiscing elit, sed do eiusmod</p><div class="meta"><span>📍&#xFE0E; Los Angeles, Califonia</span><span class="price">$370,000</span></div></div>
    <div class="card"><div class="photo" role="img" aria-label="Photo of a modern house with pool at dusk" style="background:linear-gradient(180deg,#8da2b8,#b0855a 55%,#8a9aa0)"></div><p>Lorem ipsum dolor sit amet, consetur adipiscing elit, sed do eiusmod</p><div class="meta"><span>📍&#xFE0E; Los Angeles, Califonia</span><span class="price">$370,000</span></div></div>
    <div class="card"><div class="photo" role="img" aria-label="Photo of a white modern house with pool" style="background:linear-gradient(180deg,#6ea3d8,#eaeaea 50%,#4fa6c6)"></div><p>Lorem ipsum dolor sit amet, consetur adipiscing elit, sed do eiusmod</p><div class="meta"><span>📍&#xFE0E; Los Angeles, Califonia</span><span class="price">$370,000</span></div></div>
    <div class="card"><div class="photo" role="img" aria-label="Photo of glass office towers" style="background:linear-gradient(180deg,#4c79b6,#7e8ea4 55%,#3e4a5a)"></div><p>Lorem ipsum dolor sit amet, consetur adipiscing elit, sed do eiusmod</p><div class="meta"><span>📍&#xFE0E; Los Angeles, Califonia</span><span class="price">$370,000</span></div></div>
    <div class="card"><div class="photo" role="img" aria-label="Photo of a large family house with trees" style="background:linear-gradient(180deg,#5f95d6,#a99a8a 55%,#4f8a3a)"></div><p>Lorem ipsum dolor sit amet, consetur adipiscing elit, sed do eiusmod</p><div class="meta"><span>📍&#xFE0E; Los Angeles, Califonia</span><span class="price">$370,000</span></div></div>
  </div>
</section>
<section class="news">
  <h2>LATEST NEWS</h2>
  <article class="item" style="left:99px">
    <div class="photo" role="img" aria-label="Photo of a resort building with palm trees and pool" style="background:linear-gradient(180deg,#7fb2e0,#e4e0d6 50%,#3a9bb8)"></div>
    <div><h4>Nulla at diam ornare, aliquam urna</h4><div class="date">AUG 25, 2016</div><p>Nulla at diam ornare, aliquam urna vel, commodo urna. Nam id risus a est luctus consectetur quis eget libero. Suspendisse potenti. Pellentesque habitant morbi tristique senectus</p><div class="more">Read More +</div></div>
  </article>
  <article class="item" style="left:630px">
    <div class="photo" role="img" aria-label="Photo of a white modern house with pool" style="background:linear-gradient(180deg,#6ea3d8,#eaeaea 50%,#4fa6c6)"></div>
    <div><h4>Nulla at diam ornare, aliquam urna</h4><div class="date">AUG 25, 2016</div><p>Nulla at diam ornare, aliquam urna vel, commodo urna. Nam id risus a est luctus consectetur quis eget libero. Suspendisse potenti. Pellentesque habitant morbi tristique senectus</p><div class="more">Read More +</div></div>
  </article>
</section>
<footer class="footer">
  <div class="brand"><span class="name">Corvin Lake</span><span class="sub">Real Estate</span></div>
  <p class="blurb">Lorem ipsum dolor sit amet, consectetur adipiscing elit, sed do eiusmod tempor incididunt ut labore et dolore magna aliqua. Ut enim ad minim veniam, quis nostrud Lorem ipsum dolor sit amet.</p>
  <div class="fcol" style="left:405px">
    <h5>CONTACT US</h5>
    <div>Corvin Lake</div><div>4410 Elm Court</div>
    <div class="row" style="margin-top:6px"><svg width="16" height="16" viewBox="0 0 16 16"><path d="M3 2c1-1 2 0 3 2s0 2-1 3c1 2 2 3 4 4 1-1 1-2 3-1s2 2 1 3c-2 2-5 1-7-1S1 5 3 2z" fill="none" stroke="#fff" stroke-width="1.2"/></svg>+1 555 014 7782</div>
    <div class="row"><svg width="16" height="12" viewBox="0 0 16 12"><rect x=".6" y=".6" width="14.8" height="10.8" fill="none" stroke="#fff" stroke-width="1.2"/><path d="M1 1l7 6 7-6" fill="none" stroke="#fff" stroke-width="1.2"/></svg>info@corvinlake.com</div>
  </div>
  <div class="fcol" style="left:663px;line-height:24px">
    <h5>INFORMATION</h5>
    <div>HOME</div><div>ABOUT US</div><div>PROPERTIES</div><div>GALLERY</div><div>CONTACT US</div>
  </div>
  <div class="fcol" style="left:850px;width:250px;line-height:19px">
    <h5>JOIN OUR NEWSLETTER</h5>
    <div>Excepteur sint occaecat cupidatat non proident, sunt in culpa qui</div>
    <div class="newsletter"><div class="field">Enter Name</div><div class="sub">SUBSCRIBE</div></div>
  </div>
</footer>
<div class="bottom">
  <div class="copy">Copyright©2016 Corvin Lake</div>
  <div class="socials"><span></span><span></span><span></span><span></span><span></span></div>
</div>
</body>
</html>
```